Tovanel 30ml pipette jar Mental Health

Label and Box for 30ml amber jar with pipette.
Already have a sample design, that needs to be adapted and possibly improved for the new packaging.
Dark brown letters on White Label.
The jar 30ml with pipette / dropper is amber with dark cap. Please view the photo.
Please view all the files, which I am uploading.
Please provide a mock up version.
Thank you.

Target Market(s)

Upscale women 34-59

Industry/Entity Type

Nutrition, Medical

Requirements
Must have
• Conservative, Minimalistic, Luxury
Should not have
• Leaves

```html
<!DOCTYPE html>
<html lang="en">
<head>
<meta charset="utf-8">
<title>Tovanel 10MG – Dropper Label</title>
<link rel="stylesheet" href="https://fonts.googleapis.com/css2?family=Montserrat:wght@200;300;400&family=Roboto:wght@400;500&display=swap">
<style>
  :root {
    --backdrop: #e4e5ea;
    --label-white: #fbfbfb;
    --ink-dark: #2b2622;
    --ink-grey: #8a8784;
    --brand-gold: #c9a24a;
    --glow-gold-1: #f1dca0;
    --glow-gold-2: #ebd08c;
    --band-gold: #b98c2e;
  }
  * { box-sizing: border-box; margin: 0; padding: 0; }
  html, body {
    width: 1200px;
    height: 1200px;
    overflow: hidden;
    background: var(--backdrop);
  }
  .label {
    position: absolute;
    left: 280px;
    top: 180px;
    width: 640px;
    height: 840px;
    background: var(--label-white);
    box-shadow: 0 10px 40px rgba(60, 55, 50, 0.12);
    overflow: hidden;
  }
  .brand {
    position: absolute;
    left: 64px;
    top: 50px;
    display: flex;
    align-items: center;
    gap: 14px;
  }
  .brand-dot {
    width: 64px;
    height: 64px;
    border-radius: 50%;
    border: 3px solid var(--brand-gold);
  }
  .brand-name {
    font-family: "Montserrat", sans-serif;
    font-weight: 300;
    font-size: 32px;
    line-height: 1.02;
    letter-spacing: 0.02em;
    color: var(--ink-dark);
    text-transform: uppercase;
  }
  .glow {
    position: absolute;
    left: 150px;
    top: 200px;
    width: 420px;
    height: 400px;
  }
  .product-name {
    position: absolute;
    left: 60px;
    top: 350px;
    font-family: "Montserrat", sans-serif;
    font-weight: 400;
    font-size: 66px;
    letter-spacing: 0.36em;
    color: var(--ink-dark);
  }
  .product-dose {
    position: absolute;
    left: 60px;
    top: 440px;
    font-family: "Montserrat", sans-serif;
    font-weight: 200;
    font-size: 58px;
    color: var(--ink-grey);
  }
  .claims {
    position: absolute;
    left: 60px;
    top: 612px;
    font-family: "Roboto", sans-serif;
    font-size: 23px;
    line-height: 1.5;
    color: var(--ink-dark);
  }
  .volume {
    position: absolute;
    left: 62px;
    top: 730px;
    font-family: "Roboto", sans-serif;
    font-size: 20px;
    color: var(--ink-dark);
  }
  .volume-rule {
    position: absolute;
    left: 62px;
    top: 766px;
    width: 118px;
    height: 3px;
    background: var(--ink-dark);
  }
  .gold-band {
    position: absolute;
    left: 0;
    right: 0;
    bottom: 12px;
    height: 12px;
    background: linear-gradient(90deg, var(--band-gold), var(--glow-gold-1), var(--band-gold));
  }
</style>
</head>
<body>
  <main class="label">
    <div class="brand">
      <span class="brand-dot"></span>
      <span class="brand-name">Serene<br>Practice</span>
    </div>

    <svg class="glow" viewBox="0 0 420 400" aria-hidden="true">
      <circle cx="235" cy="190" r="185" fill="var(--glow-gold-1)" opacity="0.55"/>
      <circle cx="190" cy="225" r="160" fill="var(--glow-gold-2)" opacity="0.45"/>
    </svg>

    <h1 class="product-name">TOVANEL</h1>
    <p class="product-dose">10MG</p>

    <p class="claims">Doctor Formulated<br>Developed in Clinical Practice</p>

    <p class="volume">30ml</p>
    <div class="volume-rule"></div>

    <div class="gold-band"></div>
  </main>
</body>
</html>
```